Wholesale in Gold Jewellery & Gold Bullion

We are an established gold jewellery and gold bullion wholesaler selling these products to international clients. We already have a name and logo of our company, hence please view attached current card design. We need a completely new design to compliment our business and industry and the final design should be new and elegant.

Contact Information for Business Card

New card details must be same as per current card. Like logo, name, tel no. & etc.

Colors

Designer to choose colors to be used in the design.

```html
<!DOCTYPE html>
<html lang="en">
<head>
<meta charset="utf-8">
<title>Arvale &amp; Co Business Card</title>
<link rel="stylesheet" href="https://fonts.googleapis.com/css2?family=Montserrat:wght@400;500&family=Playfair+Display:wght@700&display=swap">
<style>
  :root {
    --bg: #e9e7e3;
    --card: #ffffff;
    --gold: #d99a1e;
    --gold-faint: #f4eee2;
    --ink: #3a3a3a;
    --ink-dark: #231a14;
    --brown: #2b1a12;
  }
  * { margin: 0; padding: 0; box-sizing: border-box; }
  html, body {
    width: 1200px; height: 866px; overflow: hidden;
    background: var(--bg);
  }
  .card {
    position: absolute; left: 100px; top: 147px;
    width: 1000px; height: 572px;
    background: var(--card);
    box-shadow: 0 6px 24px rgba(0,0,0,0.12);
    overflow: hidden;
    font-family: "Montserrat", sans-serif;
    color: var(--ink);
  }
  .brand-dot {
    position: absolute; left: 60px; top: 62px;
    width: 96px; height: 96px; border-radius: 50%;
    background: var(--gold);
  }
  .company-name {
    position: absolute; left: 180px; top: 88px;
    font-family: "Playfair Display", serif; font-weight: 700;
    font-size: 34px; letter-spacing: 0.5px; color: var(--ink-dark);
  }
  .backdrop-circle {
    position: absolute; left: 620px; top: 40px;
    width: 320px; height: 320px; border-radius: 50%;
    background: var(--gold-faint);
  }
  .person-name {
    position: absolute; left: 60px; top: 238px;
    font-size: 34px; font-weight: 500; letter-spacing: 1.5px;
  }
  .person-role {
    position: absolute; left: 60px; top: 282px;
    font-size: 28px; font-weight: 400; color: var(--gold);
  }
  .contact-list {
    position: absolute; left: 60px; top: 350px;
    list-style: none;
  }
  .contact-item {
    display: flex; align-items: center; gap: 18px;
    height: 36px; font-size: 21px; letter-spacing: 0.5px;
  }
  .contact-icon { width: 24px; height: 24px; flex: none; }
  .address {
    position: absolute; right: 64px; top: 410px;
    text-align: right; font-size: 20px; line-height: 1.35; letter-spacing: 0.4px;
  }
  .band { position: absolute; }
  .band-gold-long { left: 0; bottom: 0; width: 640px; height: 18px; background: var(--gold); }
  .band-brown { left: 652px; bottom: 0; width: 240px; height: 36px; background: var(--brown); }
  .band-gold-short { left: 904px; bottom: 0; width: 96px; height: 18px; background: var(--gold); }
</style>
</head>
<body>
  <div class="card">
    <div class="backdrop-circle"></div>
    <div class="brand-dot"></div>
    <div class="company-name">ARVALE &amp; CO PTE LTD</div>

    <div class="person-name">RAVEN DOSHIKAR</div>
    <div class="person-role">Director</div>

    <ul class="contact-list">
      <li class="contact-item">
        <svg class="contact-icon" viewBox="0 0 24 24" fill="none" stroke="var(--gold)" stroke-width="1.6"><rect x="6" y="2" width="12" height="20" rx="2"/><line x1="10" y1="18.5" x2="14" y2="18.5"/></svg>
        <span>+65 9100 2345</span>
      </li>
      <li class="contact-item">
        <svg class="contact-icon" viewBox="0 0 24 24" fill="var(--gold)"><path d="M7 3l3 4-2 2c1 2.5 3 4.5 5.5 5.5l2-2 4 3-2 3.5C11 19 5 13 3.5 6.5z"/></svg>
        <span>+65 6200 1000</span>
      </li>
      <li class="contact-item">
        <svg class="contact-icon" viewBox="0 0 24 24" fill="none" stroke="var(--gold)" stroke-width="1.6"><rect x="7" y="2" width="10" height="8"/><rect x="3" y="10" width="18" height="10" rx="1"/><line x1="7" y1="15" x2="17" y2="15"/></svg>
        <span>+65 6200 1001</span>
      </li>
      <li class="contact-item">
        <svg class="contact-icon" viewBox="0 0 24 24" fill="var(--gold)"><path d="M2 5h20v14H2z"/><path d="M2 5l10 8 10-8" fill="none" stroke="#fff" stroke-width="1.4"/></svg>
        <span>raven@arvaleco.com</span>
      </li>
    </ul>

    <div class="address">12 Harlow Lane,<br>Singapore 200123</div>

    <div class="band band-gold-long"></div>
    <div class="band band-brown"></div>
    <div class="band band-gold-short"></div>
  </div>
</body>
</html>
```